KRV Photography Business Card Design

I would like a business card designed in the shape of a camera.
Would like to see various camera designs. Would like to see what the card looks like in different colors. Would like to see which logo looks better on the various camera designs so please show me some with the white logo and some with the black logo. If you need a different file formats please let me know.
Project Deadline Extended Reason: My grandfather passed away and dealing with funeral plans so need to extend deadline. Added Tuesday, March 1, 2016
Project Deadline Extended
Reason: I just got back from out of town. My grandfather's passing was the primary focus for me these past few weeks and the funeral is over so now I will concentrate on picking my business card design. I really appreciate each designer who has taken the time to submit a design. Your effort has not gone unnoticed. I look forward to seeing more amazing designs.
Business
Contact Information for Business Card
Dorine
555-418-2706
https://www.facebook.com/krvphotographyfreelance/
MonaDorine@krv-photography.example

```html
<!DOCTYPE html>
<html lang="en">
<head>
<meta charset="utf-8">
<title>KRV Photography Business Card</title>
<link rel="stylesheet" href="https://fonts.googleapis.com/css2?family=Maven+Pro:wght@400;700&display=swap">
<style>
  :root {
    --stage: #e6e2dd;
    --card-light: #ffffff;
    --card-dark: #202020;
    --accent: #b8732a;
    --gold: #d8a646;
    --gold-deep: #a9762a;
    --ink: #555555;
    --mark-light: #6e6e6e;
    --mark-dark: #8a8a8a;
  }
  html, body {
    margin: 0;
    padding: 0;
    width: 1200px;
    height: 1000px;
    overflow: hidden;
    background: var(--stage);
  }
  .stage {
    position: relative;
    width: 1200px;
    height: 1000px;
  }
  .card {
    position: absolute;
    left: 275px;
    width: 650px;
    height: 372px;
    font-family: "Maven Pro", sans-serif;
  }
  .card-front { top: 112px; background: var(--card-light); }
  .card-back  { top: 516px; background: var(--card-dark); }

  .crop-marks {
    position: absolute;
    inset: 0;
    width: 650px;
    height: 372px;
  }
  .card-front .crop-marks path { stroke: var(--mark-light); }
  .card-back .crop-marks path { stroke: var(--mark-dark); }

  .contact {
    position: absolute;
    top: 110px;
    left: 0;
    right: 0;
    text-align: center;
  }
  .contact-name {
    margin: 0 0 10px;
    font-size: 23px;
    font-weight: 700;
    color: var(--accent);
    letter-spacing: 0.3px;
  }
  .contact-line {
    margin: 0;
    font-size: 16.5px;
    line-height: 28.7px;
    color: var(--ink);
    letter-spacing: 0.4px;
  }
  .social-dot {
    display: inline-block;
    width: 9px;
    height: 12px;
    margin-right: 5px;
    background: var(--ink);
    vertical-align: -1px;
  }

  .brand {
    position: absolute;
    top: 122px;
    left: 0;
    right: 0;
    text-align: center;
  }
  .brand-dot {
    display: block;
    width: 86px;
    height: 86px;
    margin: 0 auto 14px;
    border-radius: 50%;
    background: radial-gradient(circle at 35% 30%, var(--gold), var(--gold-deep));
  }
  .brand-name {
    margin: 0;
    font-size: 25px;
    font-weight: 400;
    color: var(--gold);
    letter-spacing: 1.5px;
  }
</style>
</head>
<body>
<main class="stage">
  <section class="card card-front">
    <svg class="crop-marks" viewBox="0 0 650 372" fill="none" stroke-width="1.5" aria-hidden="true">
      <path d="M31 56V31H56"/>
      <path d="M594 31H619V56"/>
      <path d="M31 316V341H56"/>
      <path d="M594 341H619V316"/>
    </svg>
    <div class="contact">
      <p class="contact-name">Dorine</p>
      <p class="contact-line">555-418-2706</p>
      <p class="contact-line"><span class="social-dot" aria-hidden="true"></span>/krvphotographyfreelance</p>
      <p class="contact-line">MonaDorine@krv-photography.example</p>
      <p class="contact-line">krvphotography.portfolio.example</p>
    </div>
  </section>

  <section class="card card-back">
    <svg class="crop-marks" viewBox="0 0 650 372" fill="none" stroke-width="1.5" aria-hidden="true">
      <path d="M31 56V31H56"/>
      <path d="M594 31H619V56"/>
      <path d="M31 316V341H56"/>
      <path d="M594 341H619V316"/>
    </svg>
    <div class="brand">
      <span class="brand-dot" aria-hidden="true"></span>
      <p class="brand-name">KRV PHOTOGRAPHY</p>
    </div>
  </section>
</main>
</body>
</html>
```